New Business Card Design Project

We require a business card design for Vexalund, a newly established Indian company.
Our focus is on the development, manufacturing, and export of a diverse array of pharmaceutical products on a global scale. The card should convey a professional appearance, as our primary markets are in Africa, China, and Southeast Asian nations.
We envision a two-sided business card, with the reverse side dedicated to a logo set against a solid color or an elegantly designed pattern. The corners should be rounded. We would appreciate seeing both horizontal and vertical design options. We trust the designer to utilize their expertise in creating this design.

The content for the business card is included in the attached Word file.

Target Market(s)

Our primary markets are in Africa, China, and Southeast Asian, Latin America, Maldives, Sri Lanka

Industry/Entity Type

Pharmaceutical Manufacturing and Export

Contact Information for Business Card

Colors

Designer to choose colors to be used in the design.

Requirements
Must have
• The reverse side of the business card features solely the logo along with the tagline, "Care Beyond Borders."
Should not have
• The logo should not exceed two instances, encompassing both the front and back sides of the card.

```html
<!DOCTYPE html>
<html lang="en">
<head>
<meta charset="UTF-8">
<title>Vexalund Business Card</title>
<link href="https://fonts.googleapis.com/css2?family=Poppins:wght@400;600;700&display=swap" rel="stylesheet">
<style>
  :root {
    --bg: #bdbdbd;
    --brand-blue: #27a6e0;
    --brand-coral: #f2604a;
    --ink: #1f1f1f;
    --paper: #ffffff;
    --mauve: #8e8aa0;
  }
  * { box-sizing: border-box; margin: 0; padding: 0; }
  html, body { width: 1200px; height: 900px; overflow: hidden; }
  body {
    background: var(--bg);
    font-family: "Poppins", sans-serif;
    display: flex;
    flex-direction: column;
    align-items: center;
    justify-content: center;
    gap: 56px;
  }
  .card {
    width: 630px;
    height: 360px;
    border-radius: 34px;
    position: relative;
    overflow: hidden;
    box-shadow: 0 6px 16px rgba(0,0,0,0.25);
  }
  /* Reverse side */
  .card-back {
    background: linear-gradient(20deg, var(--brand-blue) 0%, var(--mauve) 52%, var(--brand-coral) 100%);
    display: flex;
    flex-direction: column;
    align-items: center;
    justify-content: center;
    color: var(--paper);
  }
  .back-brand {
    display: flex;
    align-items: center;
    gap: 14px;
    font-size: 54px;
    font-weight: 700;
    letter-spacing: 0.5px;
  }
  .brand-dot {
    width: 22px; height: 22px;
    border-radius: 50%;
    background: var(--paper);
  }
  .tagline {
    margin-top: 14px;
    font-size: 17px;
    font-weight: 400;
    letter-spacing: 1.5px;
    text-transform: uppercase;
  }
  /* Front side */
  .card-front { background: var(--paper); }
  .front-brand {
    position: absolute;
    left: 56px; top: 52px;
    font-size: 58px;
    font-weight: 700;
    color: var(--brand-blue);
    line-height: 1;
  }
  .accent-bar {
    position: absolute;
    left: 0; top: 160px;
    width: 26px; height: 52px;
    background: var(--brand-coral);
  }
  .person {
    position: absolute;
    left: 56px; top: 154px;
  }
  .person-name {
    font-size: 30px;
    font-weight: 700;
    color: var(--brand-blue);
    line-height: 1.1;
  }
  .person-role {
    font-size: 20px;
    color: var(--ink);
    line-height: 1.3;
  }
  .contacts {
    position: absolute;
    left: 56px; top: 244px;
    list-style: none;
    font-size: 19px;
    color: var(--ink);
    line-height: 1.45;
  }
  .contacts li { display: flex; align-items: center; gap: 12px; }
  .contacts svg { width: 18px; height: 18px; flex: none; }
  .address {
    position: absolute;
    right: 44px; bottom: 40px;
    text-align: right;
    font-size: 18px;
    font-style: normal;
    color: var(--ink);
    line-height: 1.35;
  }
</style>
</head>
<body>
  <section class="card card-back" aria-label="Card reverse side">
    <div class="back-brand"><span class="brand-dot"></span>Vexalund</div>
    <p class="tagline">Care Beyond Borders.</p>
  </section>

  <section class="card card-front" aria-label="Card front side">
    <div class="front-brand">Vexalund</div>
    <div class="accent-bar"></div>
    <div class="person">
      <p class="person-name">Arjun K. Mehra</p>
      <p class="person-role">CEO | Vexalund</p>
    </div>
    <ul class="contacts">
      <li>
        <svg viewBox="0 0 24 24" aria-hidden="true"><path fill="#27a6e0" d="M6.6 10.8a15.1 15.1 0 0 0 6.6 6.6l2.2-2.2a1 1 0 0 1 1-.25 11.4 11.4 0 0 0 3.6.57 1 1 0 0 1 1 1V20a1 1 0 0 1-1 1A17 17 0 0 1 3 4a1 1 0 0 1 1-1h3.5a1 1 0 0 1 1 1c0 1.25.2 2.45.57 3.57a1 1 0 0 1-.25 1z"/></svg>
        +919876543210
      </li>
      <li>
        <svg viewBox="0 0 24 24" aria-hidden="true"><rect x="2" y="5" width="20" height="14" rx="1.5" fill="#27a6e0"/><path d="M3 6l9 7 9-7" fill="none" stroke="#fff" stroke-width="1.6"/></svg>
        amehra@vexalund.com
      </li>
      <li>
        <svg viewBox="0 0 24 24" aria-hidden="true"><circle cx="12" cy="12" r="9.5" fill="none" stroke="#27a6e0" stroke-width="2"/><ellipse cx="12" cy="12" rx="4" ry="9.5" fill="none" stroke="#27a6e0" stroke-width="1.6"/><path d="M2.5 12h19M4 7h16M4 17h16" stroke="#27a6e0" stroke-width="1.4"/></svg>
        https://vexalund.com/
      </li>
    </ul>
    <address class="address">
      14, Lotus Colony<br>
      Nagpur, 440010, India
    </address>
  </section>
</body>
</html>
```